Business card por a urban DJ, up scale audience target

Need a sober design, modern, conservative colors but i can consider some options, y play rnb, hip hop, EDM and top40.

Business card for contact and personal info, double sided, use logo attrached please; im 42 so i need a card acording to my age an target audience.

Target Market(s)

Adult people, up scale audience

Industry/Entity Type

Music Download

Contact Information for Business Card

Cel (318) 4207265518 www.lumadrift.com

Requirements
Must have
• open mind
Nice to have
• open mind
Should not have
• DJ

```html
<!DOCTYPE html>
<html lang="en">
<head>
<meta charset="utf-8">
<title>Luma – Business Card</title>
<link href="https://fonts.googleapis.com/css2?family=Open+Sans:wght@400;700;800&display=swap" rel="stylesheet">
<style>
  :root {
    --backdrop: #2b2b2b;
    --card: #000000;
    --ink: #c9c9c9;
    --ink-soft: #a8a8a8;
    --rule: #9a9a9a;
  }
  * { margin: 0; padding: 0; box-sizing: border-box; }
  html, body { width: 1200px; height: 900px; overflow: hidden; }
  body {
    background: var(--backdrop);
    font-family: "Open Sans", Arial, sans-serif;
    position: relative;
  }
  .card {
    position: absolute;
    left: 250px;
    width: 700px;
    height: 400px;
    background: var(--card);
    overflow: hidden;
  }
  .card--front { top: 35px; }
  .card--back { top: 465px; }

  .front-brand {
    position: absolute;
    left: 0; right: 0; top: 115px;
    text-align: center;
    color: var(--ink);
    font-weight: 800;
    font-size: 120px;
    line-height: 1;
    letter-spacing: 4px;
  }
  .front-url {
    position: absolute;
    left: 0; right: 0; top: 262px;
    text-align: center;
    color: var(--ink);
    font-size: 26px;
    letter-spacing: 7px;
  }

  .back-rule {
    position: absolute;
    left: 0; right: 0; top: 62px;
    height: 1px;
    background: var(--rule);
  }
  .contact {
    position: absolute;
    left: 40px; top: 160px;
    color: var(--ink);
  }
  .contact__name { font-weight: 700; font-size: 22px; line-height: 1.2; }
  .contact__role { font-size: 13px; color: var(--ink-soft); margin-bottom: 6px; }
  .contact__line {
    display: flex; align-items: center; gap: 8px;
    font-size: 13px; line-height: 1.6; color: var(--ink-soft);
  }
  .contact__line svg { width: 11px; height: 11px; flex: none; }
  .back-brand {
    position: absolute;
    right: 30px; top: 150px;
    color: var(--ink);
    font-weight: 800;
    font-size: 78px;
    line-height: 1;
    letter-spacing: 2px;
  }
  .equalizer {
    position: absolute;
    left: 0; bottom: 0;
    width: 700px; height: 150px;
    display: block;
  }
</style>
</head>
<body>
  <section class="card card--front">
    <div class="front-brand">LUMA</div>
    <div class="front-url">www.lumadrift.com</div>
  </section>

  <section class="card card--back">
    <div class="back-rule"></div>
    <div class="contact">
      <div class="contact__name">Marco Vell</div>
      <div class="contact__role">CEO</div>
      <div class="contact__line">
        <svg viewBox="0 0 12 12"><rect x="3" y="0.5" width="6" height="11" rx="1" fill="none" stroke="currentColor" stroke-width="1.2"/><rect x="5" y="9" width="2" height="1" fill="currentColor"/></svg>
        (318) 4207265518
      </div>
      <div class="contact__line">
        <svg viewBox="0 0 12 12"><circle cx="6" cy="6" r="5" fill="none" stroke="currentColor" stroke-width="1.1"/><ellipse cx="6" cy="6" rx="2.2" ry="5" fill="none" stroke="currentColor" stroke-width="1"/><line x1="1" y1="6" x2="11" y2="6" stroke="currentColor" stroke-width="1"/></svg>
        www.lumadrift.com
      </div>
    </div>
    <div class="back-brand">LUMA</div>
    <svg class="equalizer" viewBox="0 0 700 150" role="img" aria-label="Sound equalizer bar graphic rising from left to right">
      <defs>
        <linearGradient id="eq-fill" x1="0" y1="1" x2="0" y2="0">
          <stop offset="0" stop-color="#c9c9c9" stop-opacity="0.75"/>
          <stop offset="1" stop-color="#c9c9c9" stop-opacity="0.35"/>
        </linearGradient>
      </defs>
      <polygon points="0,150 0,95 560,10 600,10 600,150" fill="url(#eq-fill)"/>
    </svg>
  </section>
</body>
</html>
```